Brookvane Consulting Business Card Design

Business Card Design for Brookvane Consulting. Brookvane Consulting is a boutique consultancy based in Atlanta, GA., that specializes in marketing strategy, organization planning, and leadership development. We provide solutions for small businesses and startups as well as Vantage 300 companies.

http://brookvaneconsulting.com/

Target Market(s)

We provide solutions for small businesses and startups as well as Vantage 300 companies.

Industry/Entity Type

Consulting

Contact Information for Business Card

Two sided business card with priority on contact information, logo, tag line (Guidance to Plan Better, Lead Better, Grow Further)

Colors

Designer to choose colors to be used in the design.

Requirements
Must have
• contact information, logo, tag line (Guidance to Plan Better, Lead Better, Grow Further)
• Simple no over communication.
Nice to have
• I would like to see different placements of logo and creative use of both sides of the card
Should not have
• Do not put too much information on the card.

```html
<!DOCTYPE html>
<html lang="en">
<head>
<meta charset="utf-8">
<title>Brookvane Consulting Business Card</title>
<link rel="stylesheet" href="https://fonts.googleapis.com/css2?family=Roboto:wght@400;500&family=Roboto+Condensed:wght@500&display=swap">
<style>
  :root {
    --backdrop: #8b5d40;
    --card: #1d1e20;
    --card-front: #232427;
    --card-edge: #2b2c2f;
    --text-light: #f2f2f2;
    --text-soft: #e2e2e2;
    --name-grey: #9a9a9a;
    --rule: #6f6f6f;
    --band-top: #e4e4e4;
    --band-bottom: #9c9c9c;
  }
  * { margin: 0; padding: 0; box-sizing: border-box; }
  html, body {
    width: 1200px;
    height: 960px;
    overflow: hidden;
    background: var(--backdrop);
    font-family: "Roboto", Arial, sans-serif;
  }
  .canvas { position: relative; width: 1200px; height: 960px; }

  .card { position: absolute; width: 600px; overflow: hidden; }

  .wordmark {
    font-family: "Roboto", Arial, sans-serif;
    font-weight: 500;
    color: var(--text-light);
    line-height: 1;
    white-space: nowrap;
  }

  /* Front side */
  .card-front {
    left: 322px; top: 100px; height: 360px;
    background: var(--card-front);
    border: 1px solid var(--card-edge);
  }
  .card-front .texture {
    position: absolute; inset: 0;
    background: var(--card-front);
  }
  .card-front .wordmark {
    position: absolute; left: 0; right: 0; top: 145px;
    text-align: center;
    font-size: 40px;
  }
  .card-front .tagline {
    position: absolute; left: 0; right: 0; top: 289px;
    text-align: center;
    font-size: 14px; color: var(--text-soft); letter-spacing: 0.2px;
    white-space: nowrap;
  }

  /* Back side */
  .card-back {
    left: 320px; top: 493px; height: 342px;
    background: var(--card);
  }
  .card-back .wordmark {
    position: absolute; right: 32px; top: 50px;
    font-size: 34px; text-align: right;
  }
  .contact-name {
    position: absolute; left: 28px; top: 197px;
    font-family: "Roboto Condensed", Arial, sans-serif;
    font-weight: 500; font-size: 21px; color: var(--name-grey);
    letter-spacing: 0.3px;
  }
  .contact-role {
    position: absolute; left: 28px; top: 223px;
    font-size: 15px; font-weight: 500; color: var(--text-light);
  }
  .rule {
    position: absolute; left: 28px; right: 30px; top: 254px;
    height: 1px; background: var(--rule);
  }
  .contact-lines {
    position: absolute; left: 28px; top: 269px;
    font-size: 14px; line-height: 20px; color: var(--text-light);
    list-style: none;
  }
  .contact-web {
    position: absolute; right: 30px; top: 289px;
    font-size: 14px; line-height: 20px; color: var(--text-light);
  }
  .edge-band {
    position: absolute; left: 0; right: 0; bottom: 0; height: 17px;
    background: linear-gradient(var(--band-top), var(--band-bottom));
  }
</style>
</head>
<body>
<main class="canvas">
  <section class="card card-front" aria-label="Business card front">
    <div class="texture" role="img" aria-label="Subtle dark grid pattern"></div>
    <div class="wordmark">Brookvane Consulting</div>
    <p class="tagline">Guidance to Plan Better, Lead Better, Grow Further</p>
  </section>

  <section class="card card-back" aria-label="Business card back">
    <div class="wordmark">Brookvane Consulting</div>
    <h1 class="contact-name">DARREN WHITFIELD</h1>
    <p class="contact-role">Founder/Managing Director</p>
    <div class="rule"></div>
    <ul class="contact-lines">
      <li>P : 404-555-0193</li>
      <li>darren@brookvaneconsulting.com</li>
    </ul>
    <p class="contact-web">www.brookvaneconsulting.com</p>
    <div class="edge-band"></div>
  </section>
</main>
</body>
</html>
```